Business Card Design

I'm a commercial general contractor remodel offices, hotels, health clubs and stores mostly San Francisco and the peninsula
the file I down loaded is kind of what I want I like the I beam with my company name in it, that would be fine with me but if you have better Idea will look at it you never know, I'm decided to give in and change my company name to how every one knows me, I have been in business since 1991, I like the I beam logo I included one of my old card from my old company for reference for you.

BROCK CONSTRUCTION (is my company name)
Warren Pelkey contractor, LIc 514387
3148 Larkspur Row, San Bruno, California 94071
mobile, (415) 736-4052
phone (650) 514-2087
Fax, (650) 514-2088
email, brock@brockconstruction.example

```html
<!DOCTYPE html>
<html lang="en">
<head>
<meta charset="utf-8">
<title>Brock Construction — Business Card</title>
<link href="https://fonts.googleapis.com/css2?family=Source+Sans+3:wght@400;600&display=swap" rel="stylesheet">
<style>
  :root {
    --page-bg: #eef1f4;
    --card-blue: #1a87c9;
    --card-blue-deep: #0f6fae;
    --card-blue-light: #2a9ad8;
    --card-white: #ffffff;
    --card-grey: #eceff2;
    --brand-ink: #1a74bf;
    --text-light: #ffffff;
    --shadow: rgba(20, 40, 60, 0.18);
  }
  * { box-sizing: border-box; margin: 0; padding: 0; }
  html, body {
    width: 1200px;
    height: 900px;
    overflow: hidden;
    background: var(--page-bg);
    font-family: "Source Sans 3", "Myriad Pro", Arial, sans-serif;
  }
  .sheet {
    position: relative;
    width: 1200px;
    height: 900px;
  }
  .card {
    position: absolute;
    left: 320px;
    width: 560px;
    height: 320px;
    border-radius: 4px;
    overflow: hidden;
    box-shadow: 0 10px 24px var(--shadow);
  }
  /* Back of card */
  .card-back {
    top: 100px;
    background: radial-gradient(ellipse at 50% 45%, var(--card-blue-light) 0%, var(--card-blue) 45%, var(--card-blue-deep) 100%);
    display: flex;
    align-items: center;
    justify-content: center;
  }
  .brand-name {
    font-weight: 600;
    letter-spacing: 1px;
    white-space: nowrap;
  }
  .card-back .brand-name {
    color: var(--text-light);
    font-size: 34px;
  }
  /* Front of card */
  .card-front {
    top: 480px;
    background: var(--card-white);
  }
  .front-top {
    position: absolute;
    inset: 0 0 auto 0;
    height: 140px;
    background: linear-gradient(180deg, var(--card-grey) 0%, var(--card-white) 70%);
    display: flex;
    align-items: center;
    justify-content: center;
  }
  .card-front .brand-name {
    color: var(--brand-ink);
    font-size: 32px;
  }
  .front-band {
    position: absolute;
    inset: 140px 0 0 0;
    background: var(--card-blue);
    color: var(--text-light);
  }
  .holder {
    position: absolute;
    left: 24px;
    top: 16px;
    width: 240px;
    text-align: right;
    line-height: 1.25;
  }
  .holder-name {
    font-size: 23px;
    text-align: left;
    padding-left: 14px;
    margin-bottom: 2px;
  }
  .holder-line { font-size: 15px; }
  .contact-list {
    position: absolute;
    left: 290px;
    top: 20px;
    list-style: none;
    font-size: 14px;
    color: var(--text-light);
  }
  .contact-list li {
    display: flex;
    align-items: center;
    gap: 8px;
    height: 28px;
    white-space: nowrap;
  }
  .contact-icon {
    width: 16px;
    height: 16px;
    flex: none;
  }
</style>
</head>
<body>
<main class="sheet">
  <section class="card card-back" aria-label="Card back">
    <span class="brand-name">BROCK CONSTRUCTION</span>
  </section>

  <section class="card card-front" aria-label="Card front">
    <div class="front-top">
      <span class="brand-name">BROCK CONSTRUCTION</span>
    </div>
    <div class="front-band">
      <div class="holder">
        <p class="holder-name">Warren Pelkey</p>
        <p class="holder-line">Contractor,</p>
        <p class="holder-line">Llc 514387</p>
        <p class="holder-line">3148 Larkspur Row, San Bruno,</p>
        <p class="holder-line">California 94071</p>
      </div>
      <ul class="contact-list">
        <li>
          <svg class="contact-icon" viewBox="0 0 16 16" aria-hidden="true"><rect x="0.5" y="0.5" width="15" height="15" rx="3" fill="#fff"/><rect x="5" y="2.5" width="6" height="11" rx="1" fill="none" stroke="#1a87c9" stroke-width="1.2"/><circle cx="8" cy="11.5" r="0.7" fill="#1a87c9"/></svg>
          (415) 736-4052
        </li>
        <li>
          <svg class="contact-icon" viewBox="0 0 16 16" aria-hidden="true"><rect x="0.5" y="0.5" width="15" height="15" rx="3" fill="#fff"/><path d="M3.5 7c0-2 9-2 9 0l-1.5 1-1-1H6L5 8z" fill="#1a87c9"/><rect x="5" y="8.5" width="6" height="4" rx="1" fill="#1a87c9"/></svg>
          (650) 514-2087
        </li>
        <li>
          <svg class="contact-icon" viewBox="0 0 16 16" aria-hidden="true"><rect x="0.5" y="0.5" width="15" height="15" rx="3" fill="#fff"/><rect x="5" y="3" width="6" height="4" fill="none" stroke="#1a87c9" stroke-width="1.2"/><rect x="3" y="7" width="10" height="6" rx="1" fill="#1a87c9"/></svg>
          (650) 514-2088
        </li>
        <li>
          <svg class="contact-icon" viewBox="0 0 16 16" aria-hidden="true"><rect x="0.5" y="0.5" width="15" height="15" rx="3" fill="#fff"/><path d="M6.5 9.5l3-3M7 5.5l1-1a2 2 0 0 1 3 3l-1 1M9 10.5l-1 1a2 2 0 0 1-3-3l1-1" fill="none" stroke="#1a87c9" stroke-width="1.3" stroke-linecap="round"/></svg>
          brock@brockconstruction.example
        </li>
      </ul>
    </div>
  </section>
</main>
</body>
</html>
```